Nanny Share Ecommerce Website for Finding Childcare and Parents who need Childcare BrightPramHub.net

Our company needs an ecommerce website (BrightPramHub.net) for a US subscription based service strictly for nanny sharing that connects families and caregivers. The website would allow families to connect with one another as well as to search for nannies. The service would be searchable for other families by location (by radius or zip code), children demographic (age range/gender/special needs), days of week or times, after school care, school closure days (holidays), etc. The service would also be searchable for nannies based on gender, provider age range, years experience, language, hourly rate, transportation available, certification (CPR first aid), education etc. The search fields would be searchable and sortable and allow to connect with the provider (after paying subscription fee). The service would be similar to tendlyfolk.net in that it would allow for families and caregivers to post photos as well as a short bio of the themselves. There would also be a feedback/star rating mechanism to rate caregivers who have performed work for families (viewable to public). The service would be free for nannies to post their bios and only a subscription based service for families to connect with other families or with caregivers (able to view bio but need service to connect). There will be a short bio on the benefits of nanny sharing (reduced cost, increased flexibility for parents, reduced illness, increased socialization with other children vs. sole nanny), as well as Q&A section with best practices.

Target Market(s)

Families, Nannies

Industry/Entity Type

Childcare

Logo Text

Bright Pram Hub

Coding

Coded - Design and coding required

Number of Pages Required

5+ page

Requirements
Must have
• Searchable (need to be able to search for families as well as nannies), responsive, functional, easy to use, add value to families and nannies. Needs to be able to collect payment for subscription.
Nice to have
• Optimized for mobile, SEO optimized

```html
<!DOCTYPE html>
<html lang="en">
<head>
<meta charset="utf-8">
<title>Bright Pram Hub – Nanny Sharing</title>
<link href="https://fonts.googleapis.com/css2?family=Lato:wght@300;400;700&display=swap" rel="stylesheet">
<style>
:root{
  --red:#f23a3a;
  --red-soft:#ff6f6f;
  --ink:#222;
  --text:#555;
  --muted:#9a9a9a;
  --line:#e6e6e6;
  --panel:#f6f6f6;
  --white:#fff;
  --dark:#2b2b2b;
}
*{box-sizing:border-box;margin:0;padding:0}
html,body{width:1200px;height:4196px;overflow:hidden}
body{font-family:'Lato',sans-serif;color:var(--ink);background:var(--white);position:relative}
.abs{position:absolute}
.center{text-align:center}

/* header + hero */
.hero{position:absolute;left:0;top:0;width:1200px;height:615px;background:linear-gradient(120deg,#3a3430 0%,#6b5a52 35%,#8c7a70 60%,#4a403c 100%)}
.hero-shade{position:absolute;inset:0;background:linear-gradient(180deg,rgba(0,0,0,.55),rgba(0,0,0,.2) 60%,rgba(0,0,0,.35))}
.brand{position:absolute;left:78px;top:30px;display:flex;align-items:center;gap:12px;color:var(--white);font-size:22px;font-weight:400}
.brand-dot{width:28px;height:28px;border-radius:50%;background:var(--red)}
.nav{position:absolute;right:48px;top:36px;display:flex;gap:38px;font-size:15px;color:var(--white)}
.nav .active{border-bottom:2px solid var(--white);padding-bottom:4px}
.hero-title{position:absolute;left:0;width:1200px;top:135px;font-size:38px;font-weight:400;color:var(--white)}
.hero-sub{position:absolute;left:0;width:1200px;top:190px;font-size:13px;color:#ddd}
.choice{position:absolute;top:257px;width:335px;height:336px;border-radius:22px;text-align:center;padding-top:62px}
.choice.dark{left:252px;background:rgba(20,20,20,.55);color:var(--white)}
.choice.light{left:610px;background:rgba(255,255,255,.78);color:var(--ink)}
.choice h2{font-size:24px;font-weight:400;margin-bottom:14px}
.choice p{font-size:16px;line-height:1.45;width:230px;margin:0 auto}
.pill{display:inline-block;width:230px;height:48px;line-height:48px;border-radius:24px;font-size:16px;color:var(--white);position:absolute;left:52px;top:171px}
.pill.red{background:var(--red)}
.pill.black{background:var(--dark)}
.arrow{position:absolute;top:335px;width:34px;height:34px}

/* sections */
.section-title{position:absolute;left:0;width:1200px;font-size:38px;font-weight:400;color:var(--ink)}
.section-sub{position:absolute;left:0;width:1200px;font-size:12px;color:var(--muted)}
.mark{position:absolute;left:588px;width:24px;height:24px;border-radius:50%;border:2px solid var(--red-soft)}

.service{position:absolute;top:853px;width:241px;height:364px;border-radius:24px;background:var(--white);box-shadow:0 6px 24px rgba(0,0,0,.08);text-align:center}
.service.featured{background:linear-gradient(160deg,#ff4b4b,#e82e2e);color:var(--white)}
.service-icon{width:86px;height:86px;margin:46px auto 0;border-radius:12px;background:#e9e9e9}
.service.featured .service-icon{background:rgba(255,255,255,.35)}
.service h3{font-size:17px;font-weight:400;margin-top:30px}
.service p{font-size:12px;line-height:1.55;color:var(--muted);width:180px;margin:18px auto 0}
.service.featured p{color:#ffe3e3}
.small-btn{display:inline-block;margin-top:26px;width:112px;height:28px;line-height:28px;border-radius:14px;font-size:11px;background:var(--red);color:var(--white)}
.service.featured .small-btn{background:var(--white);color:var(--ink)}

.bg-reviews{position:absolute;left:0;top:1292px;width:1200px;height:750px;background:var(--white)}
.review{position:absolute;width:336px;height:330px;border-radius:22px;padding:42px 24px 0 22px;box-shadow:0 6px 24px rgba(0,0,0,.09)}
.review.white{background:var(--white)}
.review.grey{background:#f2f2f2}
.stars{color:var(--red);font-size:17px;letter-spacing:4px}
.avatar{position:absolute;right:22px;top:28px;width:86px;height:86px;border-radius:50%;background:linear-gradient(140deg,#c9d3dc,#8d9aa6);border:4px solid var(--white)}
.review h4{font-size:16px;font-weight:400;margin-top:16px}
.review .role{font-size:11px;color:var(--muted);margin-top:4px;padding-bottom:14px;border-bottom:1px solid var(--line);width:200px}
.review p{font-size:12px;line-height:1.65;color:var(--muted);margin-top:20px;width:280px}

.bg-benefits{position:absolute;left:0;top:2042px;width:1200px;height:1001px;background:var(--panel)}
.benefit-label{position:absolute;font-size:13px;font-weight:700;color:var(--ink);letter-spacing:.3px}
.benefit-desc{position:absolute;font-size:11px;line-height:1.6;color:var(--muted)}
.hub-name{position:absolute;left:0;width:1200px;top:2632px;font-size:22px;color:#555}

.faq{position:absolute;left:252px;width:699px;height:76px;border-radius:26px;background:#f2f2f2;display:flex;align-items:center;padding:0 22px}
.faq.open{background:var(--red-soft);color:var(--white)}
.faq-num{width:46px;height:46px;border-radius:50%;border:2px solid #bbb;font-size:26px;color:#999;display:flex;align-items:center;justify-content:center;flex:none}
.faq.open .faq-num{border-color:rgba(255,255,255,.8);color:var(--white)}
.faq-q{font-size:17px;margin-left:20px;flex:1;color:#555}
.faq.open .faq-q{color:var(--white)}
.faq-toggle{width:34px;height:34px;flex:none}
.faq-answer{position:absolute;left:252px;width:699px;top:3394px;font-size:13px;line-height:1.6;color:#666;text-align:center}

.footer{position:absolute;left:0;top:3854px;width:1200px;height:342px;background:var(--panel)}
.foot-brand{position:absolute;left:0;width:1200px;top:70px;display:flex;justify-content:center;align-items:center;gap:12px;font-size:24px;color:#444}
.store{position:absolute;top:136px;width:128px;height:40px;border-radius:7px;background:#111}
.social{position:absolute;top:198px;width:22px;height:22px;border-radius:50%;background:var(--red)}
.foot-nav{position:absolute;left:0;width:1200px;top:264px;display:flex;justify-content:center;gap:40px;font-size:14px;color:#444}
.copy{position:absolute;left:0;width:1200px;top:298px;font-size:13px;color:#444}
</style>
</head>
<body>

<section class="hero">
  <div class="hero-shade" role="img" aria-label="Photo of a caregiver reading a book with a young child"></div>
  <div class="brand"><span class="brand-dot"></span>Bright Pram Hub</div>
  <nav class="nav"><span class="active">Home</span><span>About Us</span><span>Services</span><span>Benefits</span><span>Reviews</span><span>FAQ's</span></nav>
  <h1 class="hero-title center">Let's get started. Choose an option</h1>
  <p class="hero-sub center">We are a US subscription based service strictly for nanny sharing that connects families and caregivers.</p>
  <svg class="arrow" style="left:50px" viewBox="0 0 34 34"><circle cx="17" cy="17" r="15" fill="none" stroke="#fff" stroke-width="2"/><path d="M20 10l-7 7 7 7" fill="none" stroke="#fff" stroke-width="2"/></svg>
  <svg class="arrow" style="left:1116px" viewBox="0 0 34 34"><circle cx="17" cy="17" r="15" fill="none" stroke="#f23a3a" stroke-width="2"/><path d="M14 10l7 7-7 7" fill="none" stroke="#f23a3a" stroke-width="2"/></svg>
  <div class="choice dark">
    <h2>I need a Nanny</h2>
    <p>Start your nanny for care in your area.</p>
    <span class="pill red">Find Care</span>
  </div>
  <div class="choice light">
    <h2>I want a Nanny job</h2>
    <p>Create a free profile and search for jobs.</p>
    <span class="pill black">Search For Nanny</span>
  </div>
</section>

<h2 class="section-title center" style="top:660px">Our Services</h2>
<p class="section-sub center" style="top:716px">Sed ut perspiciatis unde omnis iste natus error sit voluptatem accusantium doloremque laudantium</p>

<div class="service featured" style="left:70px">
  <div class="service-icon" role="img" aria-label="Child care icon"></div>
  <h3>Child Care</h3>
  <p>Sed ut perspiciatis unde omnis iste natus error sit voluptatem accusantium doloremque</p>
  <span class="small-btn">Read More</span>
</div>
<div class="service" style="left:344px">
  <div class="service-icon" role="img" aria-label="Adult and senior care icon"></div>
  <h3>Adult &amp; Senior Care</h3>
  <p>Sed ut perspiciatis unde omnis iste natus error sit voluptatem accusantium doloremque</p>
  <span class="small-btn">Read More</span>
</div>
<div class="service" style="left:615px">
  <div class="service-icon" role="img" aria-label="Pet care icon"></div>
  <h3>Pet Care</h3>
  <p>Sed ut perspiciatis unde omnis iste natus error sit voluptatem accusantium doloremque</p>
  <span class="small-btn">Read More</span>
</div>
<div class="service" style="left:887px">
  <div class="service-icon" role="img" aria-label="Home care icon"></div>
  <h3>Home Care</h3>
  <p>Sed ut perspiciatis unde omnis iste natus error sit voluptatem accusantium doloremque</p>
  <span class="small-btn">Read More</span>
</div>

<div class="bg-reviews"></div>
<h2 class="section-title center" style="top:1382px">Reviews</h2>
<p class="section-sub center" style="top:1436px">Sed ut perspiciatis unde omnis iste natus error sit voluptatem accusantium doloremque laudantium</p>
<span class="mark" style="top:1478px"></span>
<svg class="abs" style="left:0;top:1560px" width="1200" height="260" viewBox="0 0 1200 260"><path d="M0 60 C120 20 200 40 300 90 S520 230 700 180 S950 60 1200 110" fill="none" stroke="#ff6f6f" stroke-width="3"/></svg>
<div class="review white" style="left:70px;top:1536px">
  <div class="stars">★★★★★</div><div class="avatar" role="img" aria-label="Reviewer portrait"></div>
  <h4>Jones Paul</h4><div class="role">Sed ut perspiciatis unde omnis iste</div>
  <p>Sed ut perspiciatis unde omnis iste natus error sit voluptatem accusantium doloremque laudantium, totam rem aperiam, eaque ipsa quae ab illo inventore veritatis.</p>
</div>
<div class="review grey" style="left:428px;top:1614px">
  <div class="stars">★★★★★</div><div class="avatar" role="img" aria-label="Reviewer portrait"></div>
  <h4>Micheal Pans</h4><div class="role">Sed ut perspiciatis unde omnis iste</div>
  <p>Sed ut perspiciatis unde omnis iste natus error sit voluptatem accusantium doloremque laudantium, totam rem aperiam, eaque ipsa quae ab illo inventore veritatis.</p>
</div>
<div class="review grey" style="left:792px;top:1536px">
  <div class="stars">★★★★★</div><div class="avatar" role="img" aria-label="Reviewer portrait"></div>
  <h4>Joni Toms</h4><div class="role">Sed ut perspiciatis unde omnis iste</div>
  <p>Sed ut perspiciatis unde omnis iste natus error sit voluptatem accusantium doloremque laudantium, totam rem aperiam, eaque ipsa quae ab illo inventore veritatis.</p>
</div>

<div class="bg-benefits"></div>
<h2 class="section-title center" style="top:2122px">Benefits</h2>
<p class="section-sub center" style="top:2176px">Sed ut perspiciatis unde omnis iste natus error sit voluptatem accusantium doloremque laudantium</p>
<span class="mark" style="top:2206px"></span>

<svg class="abs" style="left:0;top:2300px" width="1200" height="520" viewBox="0 0 1200 520">
  <circle cx="601" cy="310" r="190" fill="none" stroke="#fff" stroke-width="4"/>
  <circle cx="601" cy="310" r="190" fill="none" stroke="#e8e8e8" stroke-width="1"/>
  <circle cx="601" cy="275" r="44" fill="none" stroke="#d8d8d8" stroke-width="2"/>
  <!-- top: cost -->
  <circle cx="601" cy="120" r="48" fill="#f8d4d4"/><circle cx="601" cy="120" r="36" fill="#f23a3a"/>
  <circle cx="601" cy="120" r="14" fill="none" stroke="#fff" stroke-width="2"/><text x="601" y="126" font-family="Lato,sans-serif" font-size="16" fill="#fff" text-anchor="middle">$</text>
  <!-- left: parents -->
  <circle cx="420" cy="273" r="36" fill="#fff"/><circle cx="414" cy="268" r="5" fill="#f23a3a"/><circle cx="427" cy="268" r="5" fill="#f23a3a"/><path d="M405 285a9 9 0 0118 0zM419 285a9 9 0 0117 0z" fill="#f23a3a"/>
  <!-- right: illness chart -->
  <circle cx="778" cy="268" r="36" fill="#fff"/><rect x="766" y="256" width="24" height="24" fill="none" stroke="#f23a3a" stroke-width="2"/><rect x="771" y="268" width="3" height="8" fill="#f23a3a"/><rect x="777" y="263" width="3" height="13" fill="#f23a3a"/><rect x="783" y="266" width="3" height="10" fill="#f23a3a"/>
  <!-- bottom: chat -->
  <circle cx="601" cy="485" r="34" fill="#fff"/><path d="M588 474h26v16h-14l-7 6v-6h-5z" fill="none" stroke="#f23a3a" stroke-width="2"/>
</svg>
<div class="hub-name center">Bright Pram Hub</div>

<div class="benefit-label center" style="left:0;width:1200px;top:2282px">REDUCED COST</div>
<div class="benefit-desc center" style="left:420px;width:360px;top:2312px">Sed ut perspiciatis unde omnis iste natus error sit voluptatem accusantium doloremque laudantium</div>
<div class="benefit-label" style="left:52px;top:2530px">INCREASED FLEXIBILITY FOR PARENTS</div>
<div class="benefit-desc" style="left:52px;width:270px;top:2556px;text-align:right">Sed ut perspiciatis unde omnis iste natus error sit voluptatem accusantium doloremque laudantium</div>
<div class="benefit-label" style="left:940px;top:2530px">REDUCED ILLNESS</div>
<div class="benefit-desc" style="left:868px;width:270px;top:2556px">Sed ut perspiciatis unde omnis iste natus error sit voluptatem accusantium doloremque laudantium</div>
<div class="benefit-label center" style="left:0;width:1200px;top:2826px;line-height:1.4">INCREASED SOCIALIZATION WITH OTHER<br>CHILDREN VS. SOLE NANNY</div>
<div class="benefit-desc center" style="left:450px;width:300px;top:2872px">Sed ut perspiciatis unde omnis iste natus error sit voluptatem accusantium doloremque laudantium</div>

<h2 class="section-title center" style="top:3102px">Faqs</h2>
<p class="section-sub center" style="top:3158px">Sed ut perspiciatis unde omnis iste natus error sit voluptatem accusantium doloremque laudantium</p>
<span class="mark" style="top:3194px"></span>

<div class="faq open" style="top:3273px">
  <span class="faq-num">1</span><span class="faq-q">Omnis iste natus error sit voluptatem accusantium doloremque ?</span>
  <svg class="faq-toggle" viewBox="0 0 34 34"><circle cx="17" cy="17" r="15" fill="none" stroke="#333" stroke-width="2"/><path d="M10 17h14" stroke="#333" stroke-width="2"/></svg>
</div>
<p class="faq-answer">Atur aut odit aut fugit, sed quia consequuntur magni dolores eos qui ratione voluptatem sequi nesciunt. Neque porro quisquam est, qui dolorem ipsum quia dolor sit amet, consectetur, adipisci velit, sed quia non numquam eius modi tempora incidunt ut labore et dolore magnam aliquam quaerat voluptatem.</p>
<div class="faq" style="top:3510px">
  <span class="faq-num">2</span><span class="faq-q">Totam rem aperiam, eaque ipsa quae ab illo inventore veritatis</span>
  <svg class="faq-toggle" viewBox="0 0 34 34"><circle cx="17" cy="17" r="15" fill="none" stroke="#333" stroke-width="2"/><path d="M10 17h14M17 10v14" stroke="#333" stroke-width="2"/></svg>
</div>
<div class="faq" style="top:3605px">
  <span class="faq-num">3</span><span class="faq-q">Consectetur, adipisci velit, sed quia non numquam ?</span>
  <svg class="faq-toggle" viewBox="0 0 34 34"><circle cx="17" cy="17" r="15" fill="none" stroke="#333" stroke-width="2"/><path d="M10 17h14M17 10v14" stroke="#333" stroke-width="2"/></svg>
</div>
<div class="faq" style="top:3700px">
  <span class="faq-num">4</span><span class="faq-q">Ut enim ad minima veniam, quis nostrum exercitationem ?</span>
  <svg class="faq-toggle" viewBox="0 0 34 34"><circle cx="17" cy="17" r="15" fill="none" stroke="#333" stroke-width="2"/><path d="M10 17h14M17 10v14" stroke="#333" stroke-width="2"/></svg>
</div>

<footer class="footer">
  <div class="foot-brand"><span class="brand-dot" style="width:30px;height:30px;border-radius:50%;background:var(--red)"></span>Bright Pram Hub</div>
  <span class="store" style="left:464px" role="img" aria-label="App store badge"></span>
  <span class="store" style="left:608px" role="img" aria-label="Play store badge"></span>
  <span class="social" style="left:524px"></span>
  <span class="social" style="left:554px"></span>
  <span class="social" style="left:584px"></span>
  <span class="social" style="left:614px"></span>
  <span class="social" style="left:644px"></span>
  <nav class="foot-nav"><span>Home</span><span>About Us</span><span>Services</span><span>Benefits</span><span>Reviews</span><span>FAQ's</span></nav>
  <p class="copy center">© 2018 Company Name &nbsp;|&nbsp; All Rights Reserved</p>
</footer>

</body>
</html>
```